Business Card for premium dental clinic

We are a premium dental clinic based in Brasov, Romania with more than 15 year on the market, providing quality dental treatment made by a team of more specialized dentists, working with modern equipment as a solution to beautiful and healthy teeth.

Our current logo for the clinic use 2 square with colors black and gold - dr Ternisu - studio, using family fonts Bodoni, Myriad Pro and Segoe Print.
Depending on the printing we used some gold CMYK background or gold foil picture background or a gold gradient.
We want a business card:
- eye catching business card
- distinguished business card
- premium design
- to keep the color scheme of black and gold
- to attract the customers to spent time reading the information
- modern concept

```html
<!DOCTYPE html>
<html lang="en">
<head>
<meta charset="utf-8">
<title>dr Ternisu – Business Card</title>
<link href="https://fonts.googleapis.com/css2?family=Open+Sans:wght@400;600;700&family=Roboto:wght@400&family=Roboto+Condensed:wght@400&display=swap" rel="stylesheet">
<style>
  :root {
    --backdrop: #c8cccc;
    --paper: #f6f5f1;
    --gold: #e8a417;
    --gold-light: #f3c94a;
    --gold-deep: #b88410;
    --ink: #0b0b0b;
    --text-grey: #555555;
    --logo-grey: #c9c9c9;
  }
  * { margin: 0; padding: 0; box-sizing: border-box; }
  html, body { width: 1200px; height: 824px; overflow: hidden; }
  body {
    background: var(--backdrop);
    position: relative;
    font-family: "Open Sans", sans-serif;
  }
  .card {
    position: absolute;
    top: 262px;
    width: 520px;
    height: 300px;
    background: var(--paper);
    box-shadow: 0 6px 18px rgba(0,0,0,0.18);
  }
  .card--back { left: 50px; border-bottom: 3px solid var(--gold); }
  .card--front { left: 630px; }

  /* Back side: contact details */
  .contact-block {
    position: absolute;
    left: 150px;
    top: 112px;
    display: flex;
    align-items: stretch;
  }
  .person { text-align: right; padding-right: 14px; }
  .person__name { color: var(--gold); font-weight: 600; font-size: 17px; line-height: 1.1; }
  .person__role { color: var(--ink); font-weight: 700; font-size: 10px; margin-bottom: 4px; }
  .person__address { color: var(--text-grey); font-size: 11px; line-height: 1.35; font-family: "Roboto", sans-serif; }
  .divider { width: 1px; background: #333; }
  .contacts {
    list-style: none;
    padding-left: 14px;
    padding-top: 20px;
    font-family: "Roboto", sans-serif;
    font-size: 11.5px;
    color: var(--text-grey);
    line-height: 1.4;
  }
  .contacts li { display: flex; align-items: center; gap: 7px; }
  .contacts svg { width: 9px; height: 9px; flex: none; }

  /* Front side: brand */
  .front-inner {
    position: absolute;
    inset: 12px;
  }
  .gold-foil {
    position: absolute;
    left: 0; top: 0;
    width: 56%; height: 84%;
    background: linear-gradient(135deg, var(--gold-light) 0%, var(--gold) 45%, var(--gold-deep) 75%, var(--gold-light) 100%);
  }
  .black-panel {
    position: absolute;
    right: 0; top: 0;
    width: 44%; height: 100%;
    background: var(--ink);
  }
  .name-plate {
    position: absolute;
    left: 10%; top: 22%;
    width: 48%; height: 22%;
    background: #ecebe8;
    display: flex;
    align-items: center;
    justify-content: center;
  }
  .brand-name {
    font-family: "Roboto Condensed", sans-serif;
    font-weight: 400;
    font-size: 38px;
    color: var(--ink);
    line-height: 1;
  }
  .tagline {
    position: absolute;
    right: 14px; bottom: 14px;
    font-family: "Roboto Condensed", sans-serif;
    font-size: 28px;
    color: var(--logo-grey);
  }
  .web-strip {
    position: absolute;
    left: 0; bottom: 0;
    width: 56%; height: 16%;
    display: flex;
    align-items: center;
    justify-content: center;
    font-family: "Roboto", sans-serif;
    font-size: 11px;
    letter-spacing: 5px;
    color: var(--ink);
  }
</style>
</head>
<body>

<section class="card card--back" aria-label="Card back">
  <div class="contact-block">
    <div class="person">
      <p class="person__name">Andrei Colan</p>
      <p class="person__role">President</p>
      <p class="person__address">4120 Linden Court<br>Fairbanks, Alaska 99712</p>
    </div>
    <div class="divider"></div>
    <ul class="contacts">
      <li>
        <svg viewBox="0 0 10 10"><path d="M2 1 L4 1 L4.6 3 L3.4 3.8 Q4.5 6 6.2 6.6 L7 5.4 L9 6 L9 8 Q5 9.5 1 4 Z" fill="var(--gold)"/></svg>
        555-214-7730
      </li>
      <li>
        <svg viewBox="0 0 10 10"><rect x="1" y="1" width="8" height="8" fill="none" stroke="var(--gold)" stroke-width="1.2"/></svg>
        555-318-6042
      </li>
      <li>
        <svg viewBox="0 0 10 10"><rect x="0.5" y="2" width="9" height="6.5" fill="var(--gold)"/><path d="M0.5 2 L5 5.5 L9.5 2" fill="none" stroke="#fff" stroke-width="0.8"/></svg>
        hello@ternisudental.com
      </li>
      <li>
        <svg viewBox="0 0 10 10"><circle cx="5" cy="5" r="4.5" fill="var(--gold)"/><path d="M0.5 5 H9.5 M5 0.5 Q2 5 5 9.5 M5 0.5 Q8 5 5 9.5" fill="none" stroke="#fff" stroke-width="0.7"/></svg>
        www.ternisudental.com
      </li>
    </ul>
  </div>
</section>

<section class="card card--front" aria-label="Card front">
  <div class="front-inner">
    <div class="gold-foil" role="img" aria-label="Gold foil texture background"></div>
    <div class="black-panel"></div>
    <div class="name-plate">
      <span class="brand-name">dr Ternisu</span>
    </div>
    <p class="tagline">dental clinic</p>
    <p class="web-strip">ternisudental.com</p>
  </div>
</section>

</body>
</html>
```